New Business card design to reflect rebrand

I would like a business card design with a good base colour for our new logo and also a placeholder for a profile pic of the card holder. the design needs to be editable to the point that we can easily change the picture of the person and use that design for printmerlo etc. we are looking at a metalic finish business card so will need a good base colour to bring out the finish.

Target Market(s)

prospective customers

Industry/Entity Type

Business

Contact Information for Business Card

I would like one editable design that we can change the name of the card holder and profile picture. The design need to be in a format that be send to printmerlo etc.

Our address is Fenwick Lodge, Copse Lane, Ashby Combe, GU14 3TP Tel no. 01483 556172

Requirements
Must have
• place holder for a profile pic for the card holder. in AI or preferably PSD format

```html
<!DOCTYPE html>
<html lang="en">
<head>
<meta charset="utf-8">
<title>Lindmoor – Business Card</title>
<link rel="stylesheet" href="https://fonts.googleapis.com/css2?family=Signika:wght@400;600&display=swap">
<style>
  :root {
    --orange: #e8622a;
    --navy: #3d4f6e;
    --ink: #1d1d1b;
    --white: #ffffff;
    --paper: #f7f8fa;
    --photo-fill: #eeeef1;
    --photo-frame: #222222;
    --rule: #f2c2ab;
    --stage: #e9e9ec;
  }
  * { margin: 0; padding: 0; box-sizing: border-box; }
  html, body {
    width: 1200px; height: 1200px; overflow: hidden;
    background: var(--stage);
    font-family: "Signika", sans-serif;
  }
  .sheet {
    width: 1200px; height: 1200px;
    display: flex; flex-direction: column; align-items: center; justify-content: center;
    gap: 40px;
  }
  .card {
    position: relative;
    width: 840px; height: 520px;
    overflow: hidden;
    box-shadow: 0 6px 18px rgba(0,0,0,.15);
  }

  /* Front */
  .card--front { background: linear-gradient(135deg, var(--white) 0%, var(--paper) 100%); }
  .holder-band {
    position: absolute; left: 36px; top: 0; bottom: 0; width: 80px;
    background: var(--orange);
    display: flex; align-items: center; justify-content: center;
  }
  .holder-name {
    transform: rotate(-90deg);
    white-space: nowrap;
    color: var(--white);
    font-weight: 600; font-size: 30px; letter-spacing: 5px;
  }
  .photo-slot {
    position: absolute; left: 156px; top: 26px;
    width: 232px; height: 288px;
    padding: 6px;
    background: #e4e4e6;
  }
  .photo-frame {
    width: 100%; height: 100%;
    border: 6px solid var(--photo-frame);
    background: var(--photo-fill);
    display: flex; align-items: center; justify-content: center;
  }
  .photo-label {
    transform: rotate(-45deg);
    color: #cfcfd3; font-weight: 600; font-size: 44px; letter-spacing: 8px;
  }
  .brand {
    position: absolute; left: 420px; right: 20px; top: 120px; height: 110px;
    display: flex; align-items: center; justify-content: center; gap: 16px;
  }
  .brand-mark { width: 26px; height: 26px; background: var(--orange); }
  .brand-name {
    color: var(--navy); font-weight: 600; font-size: 58px; letter-spacing: 6px;
  }
  .front-rule {
    position: absolute; left: 156px; right: 0; top: 336px;
    height: 1px; background: var(--rule);
  }
  .contact { position: absolute; left: 170px; top: 350px; color: var(--orange); font-size: 27px; }
  .contact-tel { padding-bottom: 14px; border-bottom: 1px solid var(--rule); width: 620px; }
  .contact-address { padding-top: 12px; line-height: 1.4; }

  /* Back */
  .card--back { background: var(--orange); }
  .back-stripe {
    position: absolute; left: 36px; top: 0; bottom: 0; width: 56px;
    background: var(--white);
  }
  .back-brand {
    position: absolute; left: 92px; right: 0; top: 0; bottom: 0;
    display: flex; align-items: center; justify-content: center; gap: 18px;
  }
  .back-brand .brand-mark { background: var(--ink); width: 30px; height: 30px; }
  .back-brand .brand-name { color: var(--ink); font-size: 68px; }
</style>
</head>
<body>
<main class="sheet">
  <section class="card card--front" aria-label="Business card front">
    <div class="holder-band"><span class="holder-name">CARD HOLDER NAME</span></div>
    <div class="photo-slot" role="img" aria-label="Profile photo of the card holder">
      <div class="photo-frame"><span class="photo-label">PHOTO</span></div>
    </div>
    <div class="brand">
      <span class="brand-mark"></span>
      <span class="brand-name">LINDMOOR</span>
    </div>
    <div class="front-rule"></div>
    <div class="contact">
      <p class="contact-tel">Tel. 01483 556172</p>
      <p class="contact-address">Fenwick Lodge<br>Copse Lane, Ashby Combe, GU14 3TP</p>
    </div>
  </section>

  <section class="card card--back" aria-label="Business card back">
    <div class="back-stripe"></div>
    <div class="back-brand">
      <span class="brand-mark"></span>
      <span class="brand-name">LINDMOOR</span>
    </div>
  </section>
</main>
</body>
</html>
```